Veldmark Supplies Business Card

Professional business card that stand out to our potential customers. Front and back with clean modern design

Industry/Entity Type

Oil and gas

Contact Information for Business Card

Name, address, website , office phone and cell number

Requirements
Must have
• Editable files for each employee

```html
<!DOCTYPE html>
<html lang="en">
<head>
<meta charset="utf-8">
<title>Veldmark Supplies Business Card</title>
<link rel="stylesheet" href="https://fonts.googleapis.com/css2?family=Anton&family=Archivo:wght@400;600;800&display=swap">
<style>
  :root {
    --backdrop: #adadad;
    --brand-red: #ec2326;
    --brand-blue: #08b0d3;
    --paper: #ffffff;
    --ink: #111111;
    --muted: #555555;
  }
  * { box-sizing: border-box; margin: 0; padding: 0; }
  html, body { width: 1200px; height: 1000px; overflow: hidden; }
  body { background: var(--backdrop); position: relative; font-family: "Archivo", Arial, sans-serif; }

  .card {
    position: absolute;
    width: 694px;
    height: 399px;
    background: var(--paper);
    box-shadow: 4px 5px 8px rgba(0,0,0,0.3);
    overflow: hidden;
  }
  .card--front { left: 253px; top: 73px; }
  .card--back { left: 252px; top: 519px; }

  .front-split { position: absolute; inset: 0; }
  .front-wordmark {
    position: absolute;
    top: 176px;
    font-weight: 800;
    font-size: 46px;
    line-height: 48px;
    color: var(--paper);
    letter-spacing: 1px;
    text-transform: uppercase;
    white-space: nowrap;
  }
  .front-wordmark--left { left: 24px; width: 296px; text-align: center; }
  .front-wordmark--right { left: 364px; width: 306px; text-align: center; }

  .contact {
    position: absolute;
    left: 58px;
    top: 128px;
    width: 240px;
    text-align: center;
  }
  .contact__name {
    font-family: "Anton", Impact, sans-serif;
    font-size: 33px;
    line-height: 40px;
    color: var(--ink);
  }
  .contact__position {
    font-weight: 600;
    font-size: 15px;
    letter-spacing: 1.5px;
    color: var(--ink);
    margin-top: 1px;
  }
  .contact__icons {
    display: flex;
    justify-content: center;
    gap: 3px;
    margin-top: 10px;
  }
  .contact__icons svg { width: 25px; height: 25px; }
  .contact__lines {
    margin-top: 4px;
    font-size: 14.5px;
    line-height: 18px;
    color: var(--muted);
  }
  .contact__rule {
    width: 83px;
    height: 3px;
    background: var(--brand-red);
    margin: 10px auto 9px;
  }

  .brand-block {
    position: absolute;
    left: 400px;
    top: 150px;
    display: flex;
    align-items: center;
    gap: 14px;
  }
  .brand-block__square {
    width: 46px;
    height: 46px;
    background: var(--brand-blue);
  }
  .brand-block__name {
    font-weight: 800;
    font-size: 30px;
    line-height: 34px;
    color: var(--brand-red);
    text-transform: uppercase;
  }
</style>
</head>
<body>

  <section class="card card--front" aria-label="Card front">
    <svg class="front-split" viewBox="0 0 694 399" width="694" height="399" aria-hidden="true">
      <polygon points="0,0 413,0 269,399 0,399" fill="var(--brand-red)"/>
      <polygon points="422,0 694,0 694,399 277,399" fill="var(--brand-blue)"/>
    </svg>
    <div class="front-wordmark front-wordmark--left">Veldmark</div>
    <div class="front-wordmark front-wordmark--right">Supplies</div>
  </section>

  <section class="card card--back" aria-label="Card back">
    <div class="contact">
      <h1 class="contact__name">Name Surname</h1>
      <p class="contact__position">POSITION</p>
      <div class="contact__icons">
        <svg viewBox="0 0 24 24" aria-label="Phone">
          <circle cx="12" cy="12" r="12" fill="var(--brand-red)"/>
          <rect x="8.5" y="5" width="7" height="14" rx="1.2" fill="none" stroke="#fff" stroke-width="1.6"/>
          <circle cx="12" cy="16.5" r="0.9" fill="#fff"/>
        </svg>
        <svg viewBox="0 0 24 24" aria-label="Email">
          <circle cx="12" cy="12" r="12" fill="var(--brand-red)"/>
          <rect x="6" y="8" width="12" height="8.5" fill="none" stroke="#fff" stroke-width="1.4"/>
          <polyline points="6,8 12,13 18,8" fill="none" stroke="#fff" stroke-width="1.4"/>
        </svg>
        <svg viewBox="0 0 24 24" aria-label="Website">
          <circle cx="12" cy="12" r="12" fill="var(--brand-red)"/>
          <circle cx="12" cy="12" r="6" fill="none" stroke="#fff" stroke-width="1.3"/>
          <ellipse cx="12" cy="12" rx="2.6" ry="6" fill="none" stroke="#fff" stroke-width="1.1"/>
          <line x1="6" y1="12" x2="18" y2="12" stroke="#fff" stroke-width="1.1"/>
        </svg>
      </div>
      <div class="contact__lines">
        <p>(555)410-0382</p>
        <p>sales@veldmarksupplies.com</p>
        <p>veldmarksupplies.com</p>
      </div>
      <div class="contact__rule"></div>
      <div class="contact__lines">
        <p>412 N.Birchfield Suite 5</p>
        <p>Midland, Tx 79701</p>
      </div>
    </div>

    <div class="brand-block">
      <div class="brand-block__square"></div>
      <div class="brand-block__name">Veldmark<br>Supplies</div>
    </div>
  </section>

</body>
</html>
```